Moravel Aesthetic Doctor

I require an elegant, luxurious looking business card for my aesthetic business. I am a doctor and that will set me aside from competitors. I am planning to provide home and spa based treatments to clients with high expectations. I have attached my logo.

```html
<!DOCTYPE html>
<html lang="en">
<head>
<meta charset="utf-8">
<title>Moravel Aesthetic Doctor – Business Card</title>
<link href="https://fonts.googleapis.com/css2?family=Roboto:wght@300;400;700&display=swap" rel="stylesheet">
<style>
  :root {
    --backdrop: #3b3b3d;
    --card: #1f1f21;
    --sky: #5bb8ea;
    --sky-deep: #3f9fd6;
    --text: #f2f2f2;
    --muted: #b9bcc2;
    --rule: #8c8f95;
  }
  * { margin: 0; padding: 0; box-sizing: border-box; }
  html, body { width: 799px; height: 1200px; overflow: hidden; }
  body {
    background: var(--backdrop);
    font-family: "Roboto", Arial, sans-serif;
    color: var(--text);
    position: relative;
  }
  .card {
    position: absolute;
    left: 80px;
    width: 640px;
    height: 366px;
    background: var(--card);
    border-radius: 4px;
    overflow: hidden;
    box-shadow: 0 18px 40px rgba(0,0,0,.45);
  }
  .card--front { top: 140px; }
  .card--back { top: 700px; }

  .brand {
    position: absolute;
    display: flex;
    align-items: center;
    gap: 16px;
  }
  .brand__mark {
    width: 70px; height: 70px;
    border: 3px solid var(--muted);
    border-radius: 50%;
    flex: none;
  }
  .brand__name {
    font-weight: 300;
    color: var(--muted);
    line-height: 1.05;
    letter-spacing: 3px;
    text-transform: uppercase;
  }
  .brand__name .line1 { display: block; font-size: 46px; }
  .brand__name .line2 { display: block; font-size: 22px; letter-spacing: 4px; }

  .card--front .brand { left: 150px; top: 46px; }
  .services {
    position: absolute;
    top: 178px; left: 0; right: 0;
    text-align: center;
    font-size: 17px;
    line-height: 26px;
    color: var(--text);
  }
  .band {
    position: absolute;
    left: 0; right: 0;
    top: 250px; height: 38px;
    background: var(--sky);
    color: #fff;
    font-size: 17px;
    letter-spacing: 1px;
    display: flex; align-items: center; justify-content: center;
  }

  .card--back .brand { left: 110px; top: 30px; }
  .person { position: absolute; left: 48px; top: 140px; }
  .person__name { font-size: 20px; font-weight: 700; color: var(--muted); }
  .person__name small { font-size: 11px; font-weight: 400; margin-left: 4px; }
  .person__title { font-size: 15px; color: var(--sky); margin-top: 4px; }
  .rule {
    position: absolute; left: 240px; right: 40px; top: 160px;
    height: 1px; background: var(--rule);
  }
  .contacts {
    position: absolute; left: 48px; top: 212px;
    font-size: 15px; color: var(--muted);
    display: grid; grid-template-columns: auto auto auto; column-gap: 30px; row-gap: 12px;
    align-items: center;
  }
  .contact { display: flex; align-items: center; gap: 8px; white-space: nowrap; }
  .contact svg { width: 14px; height: 14px; fill: var(--sky); flex: none; }
  .social-dot {
    width: 14px; height: 14px; border-radius: 50%; background: var(--sky); display: inline-block;
  }
  .rule--low { top: 300px; left: 48px; right: 40px; }
  .tab {
    position: absolute; right: 0; bottom: 0;
    width: 330px; height: 52px;
    background: var(--sky);
    border-top-left-radius: 26px;
    color: #fff; font-size: 17px;
    display: flex; align-items: center; justify-content: center;
  }
</style>
</head>
<body>
  <section class="card card--front" aria-label="Business card front">
    <div class="brand">
      <span class="brand__mark"></span>
      <span class="brand__name"><span class="line1">Moravel</span><span class="line2">Aesthetic Doctor</span></span>
    </div>
    <p class="services">
      Dermal Injectables &nbsp;|&nbsp; Plasma Facials &nbsp;|&nbsp; Microneedling<br>
      Skin Boosters &nbsp;|&nbsp; Excessive Sweating
    </p>
    <div class="band">HOME AND SPA BASED TREATMENTS</div>
  </section>

  <section class="card card--back" aria-label="Business card back">
    <div class="brand">
      <span class="brand__mark"></span>
      <span class="brand__name"><span class="line1">Moravel</span><span class="line2">Aesthetic Doctor</span></span>
    </div>
    <div class="person">
      <p class="person__name">Dr Elena Marsh<small>MRCPCH MD</small></p>
      <p class="person__title">Australasian Diploma of Aesthetic Medicine</p>
    </div>
    <div class="rule"></div>
    <div class="contacts">
      <span class="contact">
        <svg viewBox="0 0 24 24"><path d="M6.6 10.8a15.1 15.1 0 0 0 6.6 6.6l2.2-2.2a1 1 0 0 1 1-.25 11.4 11.4 0 0 0 3.6.57 1 1 0 0 1 1 1V20a1 1 0 0 1-1 1A17 17 0 0 1 3 4a1 1 0 0 1 1-1h3.5a1 1 0 0 1 1 1c0 1.25.2 2.45.57 3.57a1 1 0 0 1-.25 1z"/></svg>
        0800 555 014
      </span>
      <span class="contact">
        <svg viewBox="0 0 24 24"><path d="M2 5h20v14H2z M2 5l10 8 10-8" fill="none" stroke="#5bb8ea" stroke-width="2"/></svg>
        elena@moravel.co.nz
      </span>
      <span class="contact">
        <svg viewBox="0 0 24 24"><circle cx="12" cy="12" r="9" fill="none" stroke="#5bb8ea" stroke-width="2"/><path d="M3 12h18M12 3c3 3 3 15 0 18M12 3c-3 3-3 15 0 18" fill="none" stroke="#5bb8ea" stroke-width="1.6"/></svg>
        www.moravel.co.nz
      </span>
      <span class="contact">Follow us on: <span class="social-dot"></span><span class="social-dot"></span></span>
    </div>
    <div class="tab">Home &amp; Spa Based Treatments</div>
  </section>
</body>
</html>
```